Defense Attorney Business Card Design Project/ Stationary

I am looking for a distinctive business card design for my solo law practice.
I practice criminal defense, both juvenile and adult, including DUI. I am a very experienced attorney with prior military experience. The design should convey a traditional, old school flair, but not be too stodgy or uptight. Some color. My logo should appear.
Updates

Project Deadline Extended Reason: I misunderstood how this project works and I was not prepared with my logo when this project ran the first time. Added Thursday, November 13, 2014

Project Deadline Extended
Reason: I was sent overseas on military duty last year, which interrupted this project. Thank you for your participation... I hope we can get this done this week! Thank you, Neil

Target Market(s)

Regular everyday people looking for strong, knowledgeable, authoritative representation while they are faced with criminal charges. Many have never been charged with a crime before. A reassuring air is therefore desired.

Industry/Entity Type

Business

Contact Information for Business Card

My information is:
Theodore M. Quill, Attorney at Law
785 Birch Avenue Suite 300
Oakland, California 94719
Tel: (510) 384-6125
Fax: (510) 391-7802
email: neilquilllaw@mailvine.example
web: www.neilquilllaw.example

Font styles to use
Serif
Sans Serif
Decorative

Colors
0255a3
ffffff

Requirements
Must have
• Sharp lines, bold elements. Conservative use of colors, such as deep blues, burgundy, grays for example.
• While my logo says "Theodore M. Quill", it should be modified to show "Theodore M. Quill".
Should not have
• Cliche imagery such as scales of justice, gavels, Statue of Liberty, etc.

```html
<!DOCTYPE html>
<html lang="en">
<head>
<meta charset="utf-8">
<title>Theodore M. Quill Law – Business Card</title>
<link rel="stylesheet" href="https://fonts.googleapis.com/css2?family=Cinzel:wght@400&family=Crimson+Text:wght@400&display=swap">
<style>
  :root {
    --page-bg: #e9ecf0;
    --front-bg: #b8d1ee;
    --front-stripe: #c9ddf3;
    --front-ink: #76818e;
    --front-ink-strong: #5f6a77;
    --back-bg: #8d8f92;
    --back-ink: #c4d8f0;
    --shadow: rgba(20, 40, 80, 0.18);
  }
  * { box-sizing: border-box; margin: 0; padding: 0; }
  html, body { width: 1200px; height: 1000px; overflow: hidden; }
  body {
    background: var(--page-bg);
    display: flex;
    align-items: center;
    justify-content: center;
    gap: 60px;
  }
  .card {
    position: relative;
    width: 525px;
    height: 300px;
    border-radius: 3px;
    box-shadow: 0 6px 18px var(--shadow);
    overflow: hidden;
  }

  /* Front side */
  .card--front { background: var(--front-bg); color: var(--front-ink); }
  .stripes {
    position: absolute; left: 0; right: 0; height: 26px;
    display: flex; flex-direction: column; justify-content: space-between;
  }
  .stripes span { display: block; height: 4px; background: var(--front-stripe); }
  .stripes--top { top: 18px; }
  .stripes--bottom { bottom: 18px; }

  .front-brand {
    position: absolute; top: 62px; right: 44px;
    display: flex; align-items: center; gap: 7px;
    font-family: 'Cinzel', serif; font-weight: 400; font-size: 15px;
    color: var(--front-ink-strong);
  }
  .front-brand .brand-dot {
    width: 10px; height: 10px; border-radius: 50%; background: var(--front-ink-strong);
  }

  .attorney-name {
    position: absolute; top: 104px; left: 30px; right: 44px;
    font-family: 'Cinzel', serif; font-weight: 400; font-size: 24px;
    letter-spacing: 0.5px; text-align: right; color: var(--front-ink);
    white-space: nowrap;
  }
  .contact {
    position: absolute; top: 152px; right: 44px; left: 30px;
    font-family: 'Crimson Text', serif; font-size: 12.5px; line-height: 1.45;
    text-align: right;
  }
  .contact p { white-space: nowrap; }
  .contact .gap { margin-top: 6px; }

  /* Back side */
  .card--back { background: var(--back-bg); color: var(--back-ink); }
  .back-brand {
    position: absolute; inset: 0;
    display: flex; align-items: center; justify-content: center; gap: 12px;
    font-family: 'Cinzel', serif; font-weight: 400; font-size: 28px;
    color: var(--back-ink); white-space: nowrap;
  }
  .back-brand .brand-dot {
    width: 18px; height: 18px; border-radius: 50%; background: var(--back-ink);
  }
</style>
</head>
<body>
  <section class="card card--front" aria-label="Business card front">
    <div class="stripes stripes--top"><span></span><span></span><span></span></div>

    <div class="front-brand"><span class="brand-dot"></span>Theodore M. Quill Law</div>

    <h1 class="attorney-name">Theodore M. Quill, Attorney</h1>

    <div class="contact">
      <p>785 Birch Avenue Suite 300</p>
      <p>Oakland, California 94719</p>
      <p class="gap">Tel: (510) 384-6125 &nbsp;Fax: (510) 391-7802</p>
      <p>Email: neilquilllaw@mailvine.example &nbsp;Web: www.neilquilllaw.example</p>
    </div>

    <div class="stripes stripes--bottom"><span></span><span></span><span></span></div>
  </section>

  <section class="card card--back" aria-label="Business card back">
    <div class="back-brand"><span class="brand-dot"></span>Theodore M. Quill Law</div>
  </section>
</body>
</html>
```